MRT Property - Business Cards

Looking for a business card & general letterhead, signage etc design for our new logo.

Colours:
000a20
0056a2
00b5ef
0088ce
68cef2

Fonts:
Poppins
Karla

Please keep look and feel of new brand - example in the zip package I sent.

```html
<!DOCTYPE html>
<html lang="en">
<head>
<meta charset="utf-8">
<title>MRT Property – Business Card</title>
<link href="https://fonts.googleapis.com/css2?family=Poppins:wght@300;400;600;700&display=swap" rel="stylesheet">
<style>
  :root {
    --navy: #000a20;
    --brand-blue: #0056a2;
    --mid-blue: #0088ce;
    --sky-blue: #00b5ef;
    --pale-blue: #68cef2;
    --band-text: #d6ecf8;
    --card: #f7f9fb;
    --backdrop: #e4e1dc;
  }
  * { margin: 0; padding: 0; box-sizing: border-box; }
  html, body {
    width: 1200px;
    height: 887px;
    overflow: hidden;
    background: var(--backdrop);
    font-family: "Poppins", sans-serif;
  }
  .card {
    position: absolute;
    left: 50px;
    top: 145px;
    width: 1100px;
    height: 598px;
    background: var(--card);
    border-radius: 22px;
    overflow: hidden;
    box-shadow: 0 10px 30px rgba(0, 10, 32, 0.12);
  }
  .brand-name {
    position: absolute;
    left: 64px;
    top: 62px;
    font-weight: 600;
    font-size: 62px;
    line-height: 1;
    color: var(--brand-blue);
    letter-spacing: -0.5px;
  }
  .holder {
    position: absolute;
    right: 77px;
    top: 56px;
    text-align: right;
  }
  .holder-name {
    font-weight: 700;
    font-size: 46px;
    line-height: 1;
    letter-spacing: 0.5px;
    color: var(--navy);
  }
  .holder-name .surname { color: var(--brand-blue); }
  .holder-title {
    margin-top: 6px;
    font-weight: 400;
    font-size: 26px;
    line-height: 1.1;
    color: var(--navy);
  }
  .edge-tab {
    position: absolute;
    right: 2px;
    top: 64px;
    width: 30px;
    height: 65px;
    background: var(--brand-blue);
    border-radius: 10px 0 0 10px;
  }
  .contact-band {
    position: absolute;
    left: 0;
    top: 307px;
    width: 880px;
    height: 246px;
  }
  .contact-band svg { position: absolute; inset: 0; }
  .address {
    position: absolute;
    left: 63px;
    top: 330px;
    font-weight: 300;
    font-size: 26px;
    line-height: 35px;
    color: var(--band-text);
  }
  .contact-list {
    position: absolute;
    left: 63px;
    top: 431px;
    list-style: none;
    font-weight: 300;
    font-size: 26px;
    line-height: 34px;
    color: var(--band-text);
  }
  .contact-list li { display: flex; align-items: center; gap: 8px; }
  .contact-list svg { width: 19px; height: 19px; flex: none; }
</style>
</head>
<body>
  <div class="card">
    <div class="brand-name">MRT Property</div>

    <div class="holder">
      <div class="holder-name">DANA <span class="surname">HOLLIS</span></div>
      <div class="holder-title">Founder &amp; Principal</div>
    </div>
    <div class="edge-tab"></div>

    <div class="contact-band">
      <svg width="880" height="246" viewBox="0 0 880 246">
        <defs>
          <linearGradient id="bandFill" x1="0" y1="0" x2="1" y2="0">
            <stop offset="0" stop-color="#0066b4"/>
            <stop offset="1" stop-color="#0056a2"/>
          </linearGradient>
        </defs>
        <polygon points="0,0 872,0 822,246 0,246" fill="url(#bandFill)"/>
      </svg>
    </div>

    <div class="address">
      4120 West 87th Street<br>
      #22, Suite Lenexa
    </div>

    <ul class="contact-list">
      <li>
        <svg viewBox="0 0 24 24" fill="none" stroke="#68cef2" stroke-width="2" stroke-linecap="round" stroke-linejoin="round"><path d="M6 3h3l2 5-2.5 1.5a11 11 0 0 0 6 6L16 13l5 2v3a2 2 0 0 1-2 2A16 16 0 0 1 4 5a2 2 0 0 1 2-2z"/></svg>
        +1- 555-013-2946
      </li>
      <li>
        <svg viewBox="0 0 24 24" fill="none" stroke="#68cef2" stroke-width="2" stroke-linejoin="round"><rect x="3" y="6" width="18" height="12" rx="1"/><path d="M3 7l9 6 9-6"/></svg>
        info@mrtproperty.com
      </li>
      <li>
        <svg viewBox="0 0 24 24" fill="none" stroke="#68cef2" stroke-width="2"><circle cx="12" cy="12" r="9"/><path d="M3 12h18M12 3c3 3 3 15 0 18M12 3c-3 3-3 15 0 18"/></svg>
        www.mrtproperty.com
      </li>
    </ul>
  </div>
</body>
</html>
```